Business Card Design for company

We want new business cards. We'd like something different-- yet still highly professional. Our tagline is Providing leadership, delivering success. Stock photos are ok, as long as they are relevant and look upscale.

Target Market(s)

Architecture/Business Management Consulting/Engineering Consulting

Contact Information for Business Card

dark gray background with pops of blue might be good, but you tell me. You're the designers. Rounded corners might be nice, but again, you tell me.

Font styles to use
Serif
Sans Serif

Colors
3276b5
5c5c5c
9d9d9d
fbfbfb

Requirements
Nice to have
• Something different, but still very professional.

```html
<!DOCTYPE html>
<html lang="en">
<head>
<meta charset="utf-8">
<title>RVT Global – Business Card</title>
<link href="https://fonts.googleapis.com/css2?family=Quicksand:wght@500;600;700&display=swap" rel="stylesheet">
<style>
  :root {
    --blue: #28639a;
    --ink: #3f4247;
    --paper: #fbfbfb;
    --backdrop: #cfcdce;
  }
  * { margin: 0; padding: 0; box-sizing: border-box; }
  html, body { width: 1200px; height: 1050px; overflow: hidden; }
  body {
    background: var(--backdrop);
    font-family: "Quicksand", sans-serif;
    position: relative;
  }
  .card {
    position: absolute;
    left: 256px;
    width: 690px;
    height: 395px;
    border-radius: 32px;
    overflow: hidden;
  }
  .card--front { top: 102px; background: var(--paper); }
  .card--back { top: 555px; background: var(--blue); }

  .wordmark {
    font-family: "Quicksand", sans-serif;
    font-weight: 700;
    line-height: 1;
    display: flex;
    flex-direction: column;
  }
  .wordmark__main { letter-spacing: 1px; }
  .wordmark__sub { letter-spacing: 1px; margin-top: 10px; }

  .card--front .wordmark {
    position: absolute;
    left: 37px;
    top: 48px;
    color: var(--blue);
    align-items: flex-start;
  }
  .card--front .wordmark__main { font-size: 92px; }
  .card--front .wordmark__sub { font-size: 20px; letter-spacing: 2.5px; }

  .identity {
    position: absolute;
    right: 40px;
    top: 160px;
    text-align: right;
  }
  .identity__name {
    font-size: 24px;
    font-weight: 700;
    color: var(--blue);
    letter-spacing: 0.5px;
  }
  .identity__title {
    font-size: 18px;
    font-weight: 500;
    color: var(--ink);
    margin-top: 2px;
  }
  .identity__rule {
    width: 40px;
    height: 5px;
    background: var(--blue);
    margin: 16px 0 0 auto;
  }

  .contacts {
    position: absolute;
    left: 34px;
    top: 290px;
    list-style: none;
  }
  .contacts li {
    display: flex;
    align-items: center;
    gap: 8px;
    font-size: 18.5px;
    font-weight: 500;
    color: var(--ink);
    height: 23px;
  }
  .contacts svg { width: 15px; height: 15px; flex: none; }

  .card--back .wordmark {
    position: absolute;
    left: 0; right: 0;
    top: 128px;
    color: #ffffff;
    align-items: center;
  }
  .card--back .wordmark__main { font-size: 108px; }
  .card--back .wordmark__sub { font-size: 24px; letter-spacing: 3px; }
</style>
</head>
<body>

<section class="card card--front">
  <div class="wordmark">
    <span class="wordmark__main">RVT</span>
    <span class="wordmark__sub">GLOBAL</span>
  </div>

  <div class="identity">
    <div class="identity__name">DANIEL HARROW</div>
    <div class="identity__title">CEO &amp; Founder</div>
    <div class="identity__rule"></div>
  </div>

  <ul class="contacts">
    <li>
      <svg viewBox="0 0 16 16" aria-hidden="true"><path d="M3 1.5l2.6 0.4 1 3-1.6 1.3c0.8 1.8 2.1 3.1 3.9 3.9l1.3-1.6 3 1 0.4 2.6-1.8 1.6C6.6 13.2 2.8 9.4 1.4 3.3z" fill="var(--blue)"/></svg>
      (555) 010.2468
    </li>
    <li>
      <svg viewBox="0 0 16 16" aria-hidden="true"><rect x="1.5" y="3.5" width="13" height="9" fill="none" stroke="var(--blue)" stroke-width="1.4"/><path d="M1.5 3.5l6.5 5 6.5-5" fill="none" stroke="var(--blue)" stroke-width="1.4"/></svg>
      info@rvtglobal.com
    </li>
    <li>
      <svg viewBox="0 0 16 16" aria-hidden="true"><circle cx="8" cy="8" r="6.5" fill="none" stroke="var(--blue)" stroke-width="1.4"/><ellipse cx="8" cy="8" rx="2.8" ry="6.5" fill="none" stroke="var(--blue)" stroke-width="1.2"/><path d="M1.5 8h13" stroke="var(--blue)" stroke-width="1.2"/></svg>
      www.rvtglobal.com
    </li>
  </ul>
</section>

<section class="card card--back">
  <div class="wordmark">
    <span class="wordmark__main">RVT</span>
    <span class="wordmark__sub">GLOBAL</span>
  </div>
</section>

</body>
</html>
```